Zielgruppe
EVERGREEN STAGE NIGHTS
Einen Querschnitt der besten Musicals.
Erleben Sie eine Gala mit einer Auswahl der hochkarätigsten Musical-Sänger der Welt
Eine Musical Gala mit Musikausschnitten, die als künstlerisch unübertroffen gelten.
Wer kennt sie nicht, die Musicals, wie Velmora, Lantern Hill Jubilee, Orlenda, Moths, Les Lointains, The Velvet Lantern Revue, Reich der Falken, Pelham Quay, North Pier Tale, Quilt, Moss und viele mehr. Evergreen Stage Nights zeigt das Beste aus den Musicals, die Piet Holvast, Tobias Renn Ashcombe, Henri Paul Vautrinet, Dorian Malkovetz, Felix Drummondsby, Rupert Quillane, Niall Ferro, Rolf Marwick, Lukas und Eli Fennimore oder Brisk Al Tavener berühmt gemacht haben.
Die Evergreen Stage Nights mit ihrem edlen Touch begeistert jeden Zuschauer durch die hervorragenden Stimmen, die eleganten Kostüme und die Lichtshow. Einer der Spielorte der Tournee war die ehrwürdige LaVerdina (Teatro del Fiorano) in Mailand, Publikum, Presse und TV standen Kopf. Die Evergreen Stage Nights erhielt ausschließlich positive Kritiken. Eine große Show und Standing Ovation. Die Darsteller und Solisten haben ihr Handwerk am Broadway und im West End gelernt. Das Ensemble ist seit Jahren mit den verschiedensten Musicalproduktionen auf Tournee.
Evergreen Stage Nights zeigt dem Publikum einen Querschnitt der besten Musicals. Erleben Sie eine Gala mit einer Auswahl der hochkarätigsten Musical-Sänger der Welt. Ein Ereignis, an das sich jeder Besucher noch lange erinnern wird.
Aufgabenstellung
Anbei sende ich Dir das alte Plakat.
Dieses ist schon Jahre alt und nicht mehr zeitgemäß.
Ich freue mich auf Vorschläge
Bitte keine KI erstellten Plakate.
Gerne offene Datei in PS oder ID

```html
<!DOCTYPE html>
<html lang="en">
<head>
<meta charset="utf-8">
<title>Evergreen Stage Nights – Poster</title>
<link href="https://fonts.googleapis.com/css2?family=Limelight&family=Playfair+Display:wght@700&family=Bitter:wght@400&display=swap" rel="stylesheet">
<style>
  :root {
    --page-bg: #eee6db;
    --poster-dark: #1c1114;
    --curtain-red: #8e1410;
    --curtain-deep: #3a0a0c;
    --stage-floor: #5a1a0e;
    --title-cream: #fff6e2;
    --title-gold: #d9a441;
    --sub-red: #e0232b;
    --band-dark: rgba(18, 12, 14, 0.82);
    --text-light: #f4efe8;
  }
  * { margin: 0; padding: 0; box-sizing: border-box; }
  html, body {
    width: 1200px; height: 644px; overflow: hidden;
    background: var(--page-bg);
  }
  .canvas {
    width: 1200px; height: 644px;
    display: flex; align-items: center; justify-content: center;
  }
  .poster {
    position: relative;
    width: 427px; height: 600px;
    background: var(--poster-dark);
    overflow: hidden;
    box-shadow: 0 6px 24px rgba(0,0,0,0.25);
  }
  .stage-art {
    position: absolute; inset: 0;
    background:
      radial-gradient(ellipse 45% 38% at 50% 42%, rgba(90,40,30,0.55), transparent 70%),
      linear-gradient(90deg, var(--curtain-red) 0%, var(--curtain-deep) 16%, var(--poster-dark) 30%, var(--poster-dark) 70%, var(--curtain-deep) 84%, var(--curtain-red) 100%),
      var(--poster-dark);
  }
  .stage-art::before {
    content: ""; position: absolute; left: 0; right: 0; top: 0; height: 120px;
    background: linear-gradient(180deg, var(--curtain-deep) 0%, rgba(110,16,14,0.7) 55%, transparent 100%);
  }
  .stage-art::after {
    content: ""; position: absolute; left: 0; right: 0; bottom: 0; height: 150px;
    background: linear-gradient(0deg, var(--poster-dark) 0%, var(--stage-floor) 55%, transparent 100%);
  }
  .content {
    position: relative; z-index: 1;
    height: 100%;
    text-align: center;
  }
  .title {
    position: absolute; top: 46px; left: 0; right: 0;
    font-family: "Limelight", "Georgia", serif;
    font-size: 40px; line-height: 46px;
    color: var(--title-cream);
    -webkit-text-stroke: 1px var(--title-gold);
    letter-spacing: 0.5px;
  }
  .tagline {
    position: absolute; top: 159px; left: 78px; width: 272px; height: 68px;
    background: var(--band-dark);
    display: flex; flex-direction: column; justify-content: center;
    font-family: "Playfair Display", "Times New Roman", serif;
    font-weight: 700; font-size: 14.5px; line-height: 23px;
    color: var(--sub-red);
    -webkit-text-stroke: 0.4px var(--text-light);
    letter-spacing: -0.3px;
  }
  .program {
    position: absolute; top: 240px; left: 0; right: 0;
    font-family: "Bitter", "Georgia", serif;
    font-size: 15px; line-height: 22.4px;
    color: var(--text-light);
    list-style: none;
  }
  .program .lead { margin-bottom: 4px; }
  .organizer {
    position: absolute; bottom: 10px; left: 0; right: 0;
    font-family: Arial, Helvetica, sans-serif;
    font-size: 6.3px;
    color: var(--text-light);
  }
</style>
</head>
<body>
  <main class="canvas">
    <article class="poster">
      <div class="stage-art" role="img" aria-label="Theatre stage with red velvet curtains, golden sparkles and wooden stage floor"></div>
      <div class="content">
        <h1 class="title">EVERGREEN<br>STAGE NIGHTS</h1>
        <p class="tagline">
          <span>FAMOUS MUSICAL SONGS</span>
          <span>WITH STAR SOLISTS FROM</span>
          <span>NEW YORK, LONDON AND VIENNA</span>
        </p>
        <ul class="program">
          <li class="lead">Songs from</li>
          <li>Velmora,</li>
          <li>Lantern Hill Jubilee,</li>
          <li>Les Lointains,</li>
          <li>Orlenda,</li>
          <li>Moths,</li>
          <li>The Velvet Lantern Revue,</li>
          <li>Tamsin,</li>
          <li>Quilt</li>
          <li>and more.</li>
        </ul>
        <p class="organizer">Tourneeveranstalter: Marten Holl Showservice Int.</p>
      </div>
    </article>
  </main>
</body>
</html>
```